Liron Vasek Website

Website for my son who is in 7th grade in the US. This will prepare him to show people his accomplishments when applying for a job or going to college. It should have:
* A picture (or multiple pictures)
* A resume page
* A place to share your accomplishments
* Links to his other social profiles
* A contact form

Great to include:
* Internships (show some photos of it along with what you’ve learned).
* Volunteer work.
* A side hustle that you want to highlight

Website sample I like:
https://belinamorud.sitefolio-demo.com/belinamorudtavik

Target Market(s)

For jobs and colleges admissions.

Number of Pages Required

5+ page

Colors

Designer to choose colors to be used in the design.

Requirements
Must have
• * A picture (or multiple pictures)
• * A resume page
• * A place to share your accomplishments
• * Links to his other social profiles
• * A contact form
Nice to have
• Great to include:
• * Internships (show some photos of it along with what you’ve learned).
• * Volunteer work.
• * A side hustle that you want to highlight

```html
<!DOCTYPE html>
<html lang="en">
<head>
<meta charset="utf-8">
<title>Liron Vasek</title>
<link href="https://fonts.googleapis.com/css2?family=Montserrat:wght@400;500;600&family=Lato:wght@400;700&display=swap" rel="stylesheet">
<style>
:root{
  --blue:#1a8fce;
  --blue-soft:rgba(32,140,195,.82);
  --ink:#4a4a4a;
  --body:#555;
  --muted:#888;
  --line:#dcdcdc;
  --grey-band:#f4f5f6;
  --page:#ffffff;
  --footer:#2b2b2b;
}
*{margin:0;padding:0;box-sizing:border-box}
html,body{width:1200px;height:2517px;overflow:hidden;background:var(--page)}
body{position:relative;font-family:'Lato',Arial,sans-serif;color:var(--body)}
.abs{position:absolute}

/* header */
.site-header{left:0;top:0;width:1200px;height:112px;background:#fff}
.brand{left:110px;top:38px;font-family:'Montserrat',sans-serif;font-weight:500;font-size:33px;color:var(--blue);line-height:42px}
.main-nav a{position:absolute;top:52px;font-family:'Montserrat',sans-serif;font-weight:500;font-size:12px;color:#333;text-decoration:none;letter-spacing:.2px}
.main-nav a.is-active{color:var(--blue)}

/* hero */
.hero{left:0;top:112px;width:1200px;height:658px;background:linear-gradient(100deg,#c7a74d 0%,#d9c063 18%,#4a5a7a 30%,#a19a7e 45%,#e6d88a 62%,#c9a58c 80%,#b88f7c 100%)}
.hero-card{left:608px;top:301px;width:482px;height:288px;background:var(--blue-soft);text-align:center;color:#fff}
.hero-card h1{margin-top:34px;font-family:'Montserrat',sans-serif;font-weight:500;font-size:47px;line-height:56px}
.hero-card p{margin-top:8px;font-family:'Montserrat',sans-serif;font-size:18px;line-height:32px;padding:0 30px}
.hero-btn{position:absolute;left:166px;top:188px;width:150px;height:56px;border-radius:28px;background:var(--blue);font-family:'Montserrat',sans-serif;font-size:18px;line-height:56px;color:#fff}

/* about */
.about-photo{left:158px;top:826px;width:381px;height:488px;background:linear-gradient(160deg,#e2cfa8,#d9a772 40%,#c97a5e 70%,#8fb0cf)}
.section-title{font-family:'Montserrat',sans-serif;font-weight:600;color:var(--ink);letter-spacing:.5px}
.about-title{left:587px;top:853px;font-size:35px;line-height:42px}
.rule{height:3px;background:var(--blue)}
.about-copy{left:586px;width:465px;font-size:14px;line-height:25.7px;text-align:justify;color:var(--body)}
.btn-pill{border-radius:26px;background:var(--blue);color:#fff;text-align:center;font-family:'Montserrat',sans-serif;font-weight:500}

/* highlights */
.highlights{left:0;top:1374px;width:1200px;height:531px;background:var(--grey-band)}
.card{width:312px}
.card h3{font-family:'Montserrat',sans-serif;font-weight:500;font-size:17px;color:#333;letter-spacing:.4px;line-height:20px;height:20px}
.card .media{margin-top:10px;height:227px}
.card p{margin-top:24px;font-size:13.6px;line-height:26.5px;color:var(--body);text-align:justify}
.btn-outline{display:block;margin-top:20px;width:122px;height:44px;border:1px solid var(--blue);color:var(--blue);font-family:'Montserrat',sans-serif;font-size:17px;line-height:42px;text-align:center;background:#fff}

/* contact */
.contact-title{left:0;width:1200px;top:1945px;text-align:center;font-size:35px;line-height:42px}
.map{left:154px;top:2058px;width:442px;height:322px;background:linear-gradient(135deg,#e9ecef,#dfe6da 45%,#e6e2d6 75%,#d6e2ee)}
.contact-info{left:637px;top:2060px;font-size:13.5px;line-height:25.5px;color:var(--body)}
.field{border:1px solid var(--line);background:#fff;font-size:12px;color:var(--muted);padding:0 16px;line-height:41px}
.submit{left:640px;top:2327px;width:125px;height:43px;background:var(--blue);color:#fff;font-family:'Montserrat',sans-serif;font-weight:600;font-size:15px;line-height:43px;text-align:center;letter-spacing:.5px}

/* footer */
.site-footer{left:0;top:2430px;width:1200px;height:87px;background:var(--footer)}
.copyright{left:111px;top:35px;font-size:13px;color:#eee;font-family:Arial,sans-serif}
</style>
</head>
<body>

<header class="abs site-header">
  <div class="abs brand">Liron Vasek</div>
  <nav class="main-nav">
    <a class="is-active" style="left:533px">HOME</a>
    <a style="left:618px">ABOUT US</a>
    <a style="left:727px">SERVICES</a>
    <a style="left:831px">RESUME</a>
    <a style="left:929px">BLOG</a>
    <a style="left:1008px">CONTACT US</a>
  </nav>
</header>

<section class="abs hero" role="img" aria-label="Photo of a boy leaning against a sunlit wall on a city street"></section>
<div class="abs hero-card">
  <h1>Liron Vasek</h1>
  <p>Sed ut perspiciatis unde omnis iste natus error voluptatem accusantium doloremque</p>
  <div class="hero-btn">Read More</div>
</div>

<div class="abs about-photo" role="img" aria-label="Portrait photo of a smiling boy"></div>
<h2 class="abs section-title about-title">ABOUT ME</h2>
<div class="abs rule" style="left:587px;top:910px;width:80px"></div>
<p class="abs about-copy" style="top:939px">Sed ut perspiciatis unde omnis iste natus error sit voluptatem accusantium doloremque laudantium, totam rem aperiam, eaque ipsa quae ab illo inventore veritatis et quasi architecto beatae vitae dicta sunt explicabo. Nemo enim ipsam voluptatem quia voluptas sit aspernatur aut odit aut dolores eos qui ratione voluptatem sequi nesciunt</p>
<p class="abs about-copy" style="top:1094px">Neque porro quisquam est, qui dolorem ipsum quia dolor sit amet, consectetur, adipisci velit, sed quia non numquam eius modi tempora incidunt ut labore et dolore magnam aliquam quaerat voluptatem. Ut enim ad quia non numquam minima veniam</p>
<div class="abs btn-pill" style="left:585px;top:1227px;width:167px;height:53px;line-height:53px;font-size:15px">READ MORE</div>

<section class="abs highlights">
  <div class="abs card" style="left:111px;top:48px">
    <h3>ACCOMPLISHMENTS</h3>
    <div class="media" role="img" aria-label="Photo of a student studying at a desk" style="background:linear-gradient(135deg,#dfe3e6,#b7cbe0 50%,#e8d9c4)"></div>
    <p>Sed ut perspiciatis unde omnis iste natus error sit voluptatem accusantium doloremque lau qu ae inventore veritatis et quasi</p>
    <span class="btn-outline">Read More</span>
  </div>
  <div class="abs card" style="left:445px;top:48px">
    <h3>INTERNSHIPS</h3>
    <div class="media" role="img" aria-label="Photo of students working with microscopes in a lab" style="background:linear-gradient(135deg,#eef0f2,#d6d9dc 50%,#f3f3f3)"></div>
    <p>Sed ut perspiciatis unde omnis iste natus error sit voluptatem accusantium doloremque lau qu ae inventore veritatis et quasi</p>
    <span class="btn-outline">Read More</span>
  </div>
  <div class="abs card" style="left:778px;top:48px">
    <h3>VOLUNTEER WORK</h3>
    <div class="media" role="img" aria-label="Photo of volunteers collecting litter in a park" style="background:linear-gradient(135deg,#8fae5a,#5d8a3a 45%,#3e4a3a 75%,#9fb86a)"></div>
    <p>Sed ut perspiciatis unde omnis iste natus error sit voluptatem accusantium doloremque lau qu ae inventore veritatis et quasi</p>
    <span class="btn-outline">Read More</span>
  </div>
</section>

<h2 class="abs section-title contact-title">CONTACT US</h2>
<div class="abs rule" style="left:560px;top:2001px;width:80px"></div>

<div class="abs map" role="img" aria-label="Street map showing the location"></div>
<div class="abs contact-info">
  Address : # Unit 3, Lorem ipsum Dummy Text Lorem Ispum<br>
  Lorem 1542 Street Lorem ipsum
  <div style="margin-top:10px">Phone : 000-555-0147 &nbsp;-&nbsp; Email : info@lironvasek-site.com</div>
</div>
<div class="abs field" style="left:640px;top:2166px;width:178px;height:42px">Name :</div>
<div class="abs field" style="left:640px;top:2216px;width:178px;height:42px">Email :</div>
<div class="abs field" style="left:640px;top:2266px;width:178px;height:42px">Phone :</div>
<div class="abs field" style="left:825px;top:2166px;width:220px;height:142px">Message :</div>
<div class="abs submit">SUBMIT</div>

<footer class="abs site-footer">
  <div class="abs copyright">© Copyright 2019 Liron Vasek.All Rights Reserved</div>
  <svg class="abs" style="left:878px;top:22px" width="214" height="42" viewBox="0 0 214 42" aria-label="Social profile links">
    <g fill="none" stroke="#fff" stroke-width="1.6" stroke-linecap="round" stroke-linejoin="round">
      <circle cx="21" cy="21" r="18"/>
      <circle cx="63" cy="21" r="18"/>
      <circle cx="106" cy="21" r="18"/>
      <circle cx="148" cy="21" r="18"/>
      <circle cx="191" cy="21" r="18"/>
      <!-- link -->
      <path d="M18 24l6-6"/>
      <path d="M19.5 17.5l2-2a3.5 3.5 0 0 1 5 5l-2 2"/>
      <path d="M22.5 24.5l-2 2a3.5 3.5 0 0 1-5-5l2-2"/>
      <!-- envelope -->
      <rect x="55" y="15" width="16" height="12" rx="1"/>
      <path d="M55 16l8 6 8-6"/>
      <!-- globe -->
      <circle cx="106" cy="21" r="8"/>
      <ellipse cx="106" cy="21" rx="3.5" ry="8"/>
      <path d="M98 21h16"/>
      <!-- chat bubble -->
      <path d="M140 15h16v10h-9l-4 4v-4h-3z"/>
      <!-- user -->
      <circle cx="191" cy="17" r="3.5"/>
      <path d="M184 29c0-4 3-6.5 7-6.5s7 2.5 7 6.5"/>
    </g>
  </svg>
</footer>

</body>
</html>
```